Heron Loan Partners Business Card

We need a business card design for our mortgage servicing company. In addition to servicing the loans of homeowners, we help homeowners with purchasing their homes and any mortgage refinancing. We would like to see designs that use the colors in the logo attached below (gold-ish yellow and navy blue), and any other design you deem fit! The design should communicate a simpler life with smart mortgages provided by Heron.

```html
<!DOCTYPE html>
<html lang="en">
<head>
<meta charset="utf-8">
<title>Heron Loan Partners Business Card</title>
<link href="https://fonts.googleapis.com/css2?family=Arimo:wght@400;700&display=swap" rel="stylesheet">
<style>
  :root {
    --backdrop: #3d3d3d;
    --navy: #231f55;
    --navy-soft: #2c2866;
    --gold: #e2ac2c;
    --paper: #ffffff;
    --ink: #4a4a4a;
    --light: #ffffff;
  }
  html, body {
    margin: 0;
    padding: 0;
    width: 1200px;
    height: 803px;
    overflow: hidden;
    background: var(--backdrop);
    font-family: "Arimo", Arial, sans-serif;
  }
  .stage {
    position: relative;
    width: 1200px;
    height: 803px;
  }
  .card {
    position: absolute;
    width: 520px;
    height: 297px;
    border-radius: 18px;
    box-sizing: border-box;
    border-bottom: 3px solid var(--gold);
    box-shadow: 0 14px 30px rgba(0,0,0,0.35);
    overflow: hidden;
  }
  .card--front {
    left: 70px;
    top: 150px;
    background: var(--navy);
    color: var(--light);
  }
  .card--back {
    left: 610px;
    top: 356px;
    background: var(--paper);
    color: var(--ink);
  }
  .front-illustration {
    position: absolute;
    left: 30px;
    top: 40px;
    width: 460px;
    height: 190px;
    border-radius: 50%;
    background: radial-gradient(ellipse at center, var(--navy-soft) 0%, var(--navy) 70%);
  }
  .details {
    position: absolute;
    left: 0;
    right: 0;
    top: 88px;
    display: flex;
    justify-content: center;
    align-items: stretch;
  }
  .identity {
    text-align: right;
    padding-right: 14px;
  }
  .identity__name {
    font-size: 22px;
    font-weight: 700;
    margin: 0;
  }
  .identity__title {
    font-size: 12px;
    margin: 2px 0 6px;
  }
  .identity__address {
    font-size: 12px;
    line-height: 1.35;
    margin: 0;
  }
  .divider {
    width: 1px;
    background: rgba(255,255,255,0.7);
  }
  .contacts {
    list-style: none;
    margin: 0;
    padding: 0 0 0 14px;
    font-size: 12px;
    line-height: 1.45;
  }
  .contacts li {
    display: flex;
    align-items: center;
    gap: 6px;
  }
  .contacts svg {
    width: 10px;
    height: 10px;
    fill: var(--light);
    flex: none;
  }
  .tagline {
    position: absolute;
    left: 0;
    right: 0;
    text-align: center;
    font-size: 12px;
  }
  .card--front .tagline { bottom: 42px; }
  .card--back .tagline { bottom: 50px; color: var(--ink); font-size: 13px; }
  .brand {
    position: absolute;
    left: 0;
    right: 0;
    top: 92px;
    text-align: center;
  }
  .brand__name {
    font-size: 34px;
    font-weight: 700;
    color: var(--navy);
    margin: 0;
  }
  .brand__mark {
    display: inline-block;
    width: 14px;
    height: 14px;
    border-radius: 50%;
    background: var(--gold);
    margin-right: 10px;
    vertical-align: middle;
  }
</style>
</head>
<body>
<div class="stage">
  <section class="card card--front">
    <div class="front-illustration" role="img" aria-label="Gold line drawing of a leaping fish spanning the card"></div>
    <div class="details">
      <div class="identity">
        <p class="identity__name">Daniel Brooks</p>
        <p class="identity__title">President</p>
        <p class="identity__address">4120 Willow Bend Road<br>Halton, Canada 58213</p>
      </div>
      <div class="divider"></div>
      <ul class="contacts">
        <li><svg viewBox="0 0 10 10"><path d="M2 0.5 L3.8 2.6 L2.9 3.8 Q4 6 6.2 7.1 L7.4 6.2 L9.5 8 L8.4 9.5 Q3 9 0.5 1.6 Z"/></svg>555-210-4471</li>
        <li><svg viewBox="0 0 10 10"><path d="M2.5 0.5 H7.5 V9.5 H2.5 Z M3.4 1.4 V7.6 H6.6 V1.4 Z"/></svg>555-382-9160</li>
        <li><svg viewBox="0 0 10 10"><path d="M0.5 2 H9.5 V8 H0.5 Z M1 2.4 L5 5.4 L9 2.4 Z"/></svg>info@heronloanpartners.com</li>
        <li><svg viewBox="0 0 10 10"><circle cx="5" cy="5" r="4.5"/></svg>www.heronloanpartners.com</li>
      </ul>
    </div>
    <p class="tagline">Simpler life with smart mortgages</p>
  </section>

  <section class="card card--back">
    <div class="brand">
      <p class="brand__name"><span class="brand__mark"></span>Heron Loan Partners</p>
    </div>
    <p class="tagline">Simpler life with smart mortgages</p>
  </section>
</div>
</body>
</html>
```